life insurance quote website design for lepontdoriole.ca

the web site lepontdoriole.ca need a design. we dont like the actuel one but we are open at all new suggestion. visit us at lepontdoriole.ca and you will understand. the principal concurant is tarifsgarantisnord.ca, calculeo.ca, coutprotecfam.ca. We are a life insurance quote site. we found best price available in the canadien industrie. We absolutly want a design with our form in the front page on the top right side like our concurance, we use wordpress at this time. we want to be able to switch language. and to have a logic form. we want to be able to change the color for each type of insurance quote page.we also need a blog in it to post news. and the site will be SEO accurate.

Target Market(s)

Get client fill the quote form

Industry/Entity Type

Insurance

Number of Pages Required

3 page

Font styles to use
Sans Serif

Requirements
Must have
• logic form on the top right first page
• page template for product info stuff, contact, and who we are, blog
• French site
• custum color
Nice to have
• Wordpress design will be appréciate
• switch language english/french

```html
<!DOCTYPE html>
<html lang="en">
<head>
<meta charset="utf-8">
<title>Le Pont d'Oriole – Life Insurance Quotes</title>
<link href="https://fonts.googleapis.com/css2?family=Open+Sans:wght@400;600;700;800&display=swap" rel="stylesheet">
<style>
:root{
  --red:#e41e26;
  --navy:#1b2a4a;
  --blue:#1d4f9c;
  --form:rgba(28,72,150,.92);
  --text:#555;
  --light:#f3f3f3;
  --footer:#232323;
  --life:#2fb3d6;
  --salary:#dc9a2c;
  --mortgage:#5cb85c;
  --illness:#ea5a78;
}
*{box-sizing:border-box;margin:0;padding:0}
html,body{width:1200px;height:2778px;overflow:hidden}
body{font-family:"Open Sans",Arial,sans-serif;color:var(--text);background:#fff;position:relative}
.abs{position:absolute}
.site-header{position:absolute;left:0;top:0;width:1200px;height:92px;border-top:5px solid var(--red);background:#fff}
.brand{position:absolute;left:100px;top:26px;display:flex;align-items:center;gap:10px;font-weight:800;font-size:24px;color:var(--red)}
.brand .dot{width:16px;height:16px;border-radius:50%;background:var(--red)}
.lang{position:absolute;left:546px;top:22px;display:flex;gap:14px;font-size:12px;color:#333}
.lang span{display:flex;align-items:center;gap:5px}
.flag{width:16px;height:10px;display:inline-block}
.flag.ca{background:linear-gradient(90deg,#d52b1e 25%,#fff 25%,#fff 75%,#d52b1e 75%)}
.flag.fr{background:#1a4fa0;border:1px solid #fff;box-shadow:0 0 0 1px #1a4fa0}
.contact-top{position:absolute;top:15px;display:flex;align-items:center;gap:8px;font-size:13px;color:#333}
.circle-ic{width:30px;height:30px;border-radius:50%;border:2px solid var(--red);display:flex;align-items:center;justify-content:center}
.main-nav{position:absolute;left:713px;top:60px;display:flex;gap:30px;font-size:12.5px;font-weight:700;color:#222}
.main-nav .active{color:var(--red)}
.hero{position:absolute;left:0;top:92px;width:1200px;height:470px}
.hero-photo{position:absolute;inset:0;background:linear-gradient(180deg,#7fb3e0 0%,#b9d6ee 45%,#c9c9a0 62%,#7e9a45 80%,#5e7d2c 100%)}
.hero-title{position:absolute;left:96px;top:190px;color:#fff;font-weight:800;text-shadow:0 2px 4px rgba(0,0,0,.45);text-transform:uppercase}
.hero-title .small{font-size:29px;font-weight:700;display:block;line-height:36px}
.hero-title .big{font-size:40px;display:block;line-height:48px}
.slide-arrow{position:absolute;top:222px}
.quote-form{position:absolute;left:698px;top:0;width:402px;height:470px;background:var(--form);color:#fff;padding:0 26px 0 24px}
.quote-form h2{text-align:center;font-size:21px;font-weight:700;padding-top:8px;height:48px;line-height:40px;border-bottom:2px solid #fff;margin:0 -4px}
.f-group{font-size:14px;font-weight:700;margin-top:10px;padding-bottom:4px;border-bottom:1px solid rgba(255,255,255,.5)}
.f-row{display:flex;align-items:center;height:37px;font-size:12px}
.f-row label{width:128px}
.f-row .in{width:226px;height:28px;background:#fff}
.f-row .sel{display:flex;justify-content:flex-end}
.f-row .sel i{width:28px;height:28px;background:linear-gradient(#eee,#ccc);display:flex;align-items:center;justify-content:center}
.chk{width:14px;height:14px;background:#fff;display:inline-block;vertical-align:middle;margin-right:8px;flex:none}
.opts{display:flex;gap:20px}
.co-row{display:flex;font-size:11.5px;margin-top:10px;gap:12px;line-height:16px}
.co-row div{display:flex;align-items:flex-start}
.co-row .add{white-space:nowrap;width:150px}
.send{display:block;margin:14px 0 0;height:37px;background:var(--red);text-align:center;line-height:37px;font-weight:700;font-size:15px;border-radius:3px}
.welcome{position:absolute;left:0;top:562px;width:1200px;height:543px}
.welcome h1{position:absolute;left:0;width:100%;top:35px;text-align:center;font-size:22px;font-weight:800;color:var(--navy)}
.welcome h1 span,.sec-title span{color:var(--blue)}
.welcome .intro{position:absolute;left:150px;width:900px;top:88px;text-align:center;font-size:11.5px;line-height:24px}
.service{position:absolute;top:198px;width:240px;text-align:center}
.service .badge{display:block;margin:0 auto;width:108px;height:124px;border-radius:14px 14px 54px 54px}
.service h3{margin-top:26px;font-size:15.5px;font-weight:700;color:#222}
.service p{margin-top:12px;font-size:12px;line-height:22px}
.service .bid{display:block;margin-top:14px;color:var(--red);font-weight:700;font-size:12px}
.sec-title{position:absolute;left:0;width:1200px;text-align:center;font-size:22px;font-weight:800;color:var(--navy);display:flex;justify-content:center;align-items:center;gap:26px}
.products{position:absolute;left:0;top:1105px;width:1200px;height:441px;background:var(--light)}
.prod-text{position:absolute;left:100px;top:98px;width:500px}
.prod-text h3{font-size:19px;font-weight:800;color:#222}
.prod-text h3 span{color:var(--blue)}
.prod-text h4{margin-top:12px;font-size:15px;color:#333;font-weight:700}
.prod-text p{margin-top:10px;font-size:12.5px;line-height:22px}
.prod-text ul{list-style:none;margin-top:14px}
.prod-text li{display:flex;align-items:center;gap:12px;font-size:12.5px;height:30px}
.more{color:var(--red);font-weight:700;font-size:12px}
.prod-photo{position:absolute;left:635px;top:91px;width:465px;height:310px;border:5px solid #fff;box-shadow:0 0 0 1px #ddd;background:linear-gradient(135deg,#9ac04a,#6f9a2c 50%,#c9a080)}
.blog{position:absolute;left:0;top:1546px;width:1200px;height:436px}
.post{position:absolute;top:102px;width:234px}
.post .thumb{position:relative;height:145px;border:4px solid #fff;box-shadow:0 0 0 1px #ddd}
.post .date{position:absolute;right:0;bottom:0;background:rgba(0,0,0,.75);color:#fff;font-size:11px;font-weight:700;padding:3px 8px}
.post h4{margin-top:20px;font-size:13px;font-weight:700;color:#222;line-height:18px;text-transform:uppercase;height:38px}
.post p{font-size:11.5px;line-height:19px;margin-top:4px;height:50px}
.post .more{display:block;margin-top:22px;font-size:11px}
.companies{position:absolute;left:0;top:1982px;width:1200px;height:209px;background:var(--light)}
.partner{position:absolute;top:88px;width:150px;height:73px;background:#fff;border:1px solid #ddd;display:flex;align-items:center;justify-content:center;font-size:17px;font-weight:700;color:#1d4f9c}
.offices{position:absolute;left:0;top:2191px;width:1200px;height:281px;overflow:hidden}
.offices-bg{position:absolute;inset:0;background:linear-gradient(180deg,#6aa6dc 0%,#c9e0f2 55%,#9ccd53 80%,#6ea52f 100%)}
.offices-people{position:absolute;left:741px;top:0;width:459px;height:281px;background:linear-gradient(90deg,rgba(230,200,170,0) 0%,rgba(214,176,140,.85) 30%,#c9a283 70%,#a9c46a 100%)}
.offices h2{position:absolute;left:100px;top:38px;font-size:21px;font-weight:800;color:var(--navy)}
.city-col{position:absolute;top:88px;list-style:none}
.city-col li{display:flex;align-items:center;gap:10px;height:36px;font-size:12px;font-weight:700;color:#222}
.site-footer{position:absolute;left:0;top:2472px;width:1200px;height:306px;background:var(--footer);color:#ddd}
.f-brand{position:absolute;left:100px;top:30px;font-size:19px;font-weight:800;color:#fff;width:160px;line-height:26px}
.f-badge{position:absolute;left:100px;top:136px;width:150px;height:92px;border:2px solid #777}
.f-col{position:absolute;top:42px;font-size:12.5px}
.f-col h5{font-size:14px;font-weight:700;color:#fff;margin-bottom:22px}
.hours div{display:flex;height:31px}
.hours span:first-child{width:110px}
.news p{line-height:20px;width:260px}
.news .email{margin-top:12px;width:263px;height:32px;background:#fff;color:#999;font-size:11px;padding:8px 10px}
.news .sub{margin-top:15px;width:102px;height:32px;border:2px solid #fff;text-align:center;line-height:28px;font-weight:700;color:#fff;font-size:12px}
.contact-col div{display:flex;align-items:center;gap:14px;height:47px}
.f-bottom{position:absolute;left:100px;top:241px;width:1000px;border-top:1px solid #3a3a3a}
.copy{position:absolute;left:100px;top:262px;font-size:11.5px;color:#ccc}
.social{position:absolute;left:972px;top:256px;display:flex;gap:10px}
.social i{width:28px;height:28px;border:2px solid #ddd;border-radius:50%}
</style>
</head>
<body>

<header class="site-header">
  <div class="brand"><span class="dot"></span>Le Pont d'Oriole</div>
  <div class="lang"><span><i class="flag ca"></i>English</span><span><i class="flag fr"></i>French</span></div>
  <div class="contact-top" style="left:713px">
    <span class="circle-ic"><svg width="14" height="10" viewBox="0 0 14 10"><rect x="0.5" y="0.5" width="13" height="9" fill="none" stroke="#e41e26"/><path d="M1 1l6 5 6-5" fill="none" stroke="#e41e26"/></svg></span>
    contact@lepontdoriole.ca
  </div>
  <div class="contact-top" style="left:957px">
    <span class="circle-ic"><svg width="14" height="14" viewBox="0 0 14 14"><path d="M3 1l3 3-2 2c1 2 2 3 4 4l2-2 3 3-2 2C6 13 1 8 1 3z" fill="#e41e26"/></svg></span>
    1-855-555-0142
  </div>
  <nav class="main-nav">
    <span class="active">HOME</span><span>WHO ARE WE</span><span>BLOG</span><span>CONTACT US</span>
    <svg width="14" height="14" viewBox="0 0 14 14"><circle cx="6" cy="6" r="4.5" fill="none" stroke="#222" stroke-width="2"/><path d="M9.5 9.5L13 13" stroke="#222" stroke-width="2"/></svg>
  </nav>
</header>

<section class="hero">
  <div class="hero-photo" role="img" aria-label="Family playing in a sunny green field under a blue sky"></div>
  <svg class="slide-arrow" style="left:52px" width="16" height="30" viewBox="0 0 16 30"><path d="M14 2L2 15l12 13" fill="none" stroke="#fff" stroke-width="3"/></svg>
  <svg class="slide-arrow" style="left:1148px" width="16" height="30" viewBox="0 0 16 30"><path d="M2 2l12 13L2 28" fill="none" stroke="#fff" stroke-width="3"/></svg>
  <h2 class="hero-title"><span class="small">The assurance of</span><span class="big">Getting the best price</span></h2>

  <form class="quote-form">
    <h2>QUOTE REQUEST</h2>
    <div class="f-group">Product</div>
    <div class="f-row"><label>Type of Insurance :</label><span class="in sel"><i><svg width="10" height="6"><path d="M0 0h10L5 6z" fill="#666"/></svg></i></span></div>
    <div class="f-group" style="margin-top:2px">Applicant</div>
    <div class="f-row"><label>Full Name * :</label><span class="in"></span></div>
    <div class="f-row"><label>Cities * :</label><span class="in"></span></div>
    <div class="f-row"><label>Email * :</label><span class="in"></span></div>
    <div class="f-row"><label>Phone * :</label><span class="in"></span></div>
    <div class="f-row"><label>Age * :</label><span class="in"></span></div>
    <div class="f-row" style="height:28px"><label>Gender * :</label><span class="opts"><span><i class="chk"></i>Man</span><span><i class="chk"></i>Wife</span></span></div>
    <div class="f-group" style="margin-top:0">Co-Applicant</div>
    <div class="co-row"><div class="add"><i class="chk"></i>Add a co-applicant</div><div><i class="chk"></i>I have read and accept the use and privacy policy of **</div></div>
    <span class="send">SEND</span>
  </form>
</section>

<section class="welcome">
  <h1>WELCOME TO <span>LE PONT D'ORIOLE</span></h1>
  <p class="intro">Our mission is to help our customers find the insurance that best meets their needs taking into account the best possible price. The consultant team always realize the financial needs analysis to determine the best choice of product. Conscientious and professional, they respect the laws and regulations set up by the ORF and the chamber of financial security. Their permits and licenses are checked regularly to ensure they are working legally.</p>

  <div class="service" style="left:93px">
    <span class="badge" role="img" aria-label="Life insurance service badge" style="background:linear-gradient(180deg,#d8f1f8,#8fd5ea)"></span>
    <h3>ASSURANCE VIE</h3>
    <p>A fast, free and confidential. Fill the life insurance quote form and you will enjoy your experience with us, a counselor will review your application</p>
    <span class="bid">BIDDING</span>
  </div>
  <div class="service" style="left:350px">
    <span class="badge" role="img" aria-label="Salary insurance service badge" style="background:linear-gradient(180deg,#f8ead2,#eac07a)"></span>
    <h3>SALAIRE</h3>
    <p>A fast, free and confidential. Fill the life insurance quote form and you will enjoy your experience with us, a counselor will review your application</p>
    <span class="bid">BIDDING</span>
  </div>
  <div class="service" style="left:608px">
    <span class="badge" role="img" aria-label="Mortgage insurance service badge" style="background:linear-gradient(180deg,#dcf0dc,#9ed49e)"></span>
    <h3>HYPOTHECAIRE</h3>
    <p>A fast, free and confidential. Fill the life insurance quote form and you will enjoy your experience with us, a counselor will review your application</p>
    <span class="bid">BIDDING</span>
  </div>
  <div class="service" style="left:867px">
    <span class="badge" role="img" aria-label="Critical illness insurance service badge" style="background:linear-gradient(180deg,#fbe0e6,#f19bae)"></span>
    <h3>MALADIES GRAVES</h3>
    <p>A fast, free and confidential. Fill the life insurance quote form and you will enjoy your experience with us, a counselor will review your application</p>
    <span class="bid">BIDDING</span>
  </div>
</section>

<section class="products">
  <h2 class="sec-title" style="top:30px">
    <svg width="10" height="18"><path d="M9 1L1 9l8 8" fill="none" stroke="#888" stroke-width="2"/></svg>
    <span style="color:var(--navy)">OUR <span>PRODUCTS</span></span>
    <svg width="10" height="18"><path d="M1 1l8 8-8 8" fill="none" stroke="#888" stroke-width="2"/></svg>
  </h2>
  <div class="prod-text">
    <h3>ONLINE <span>LIFE INSURANCE SUBMISSION</span></h3>
    <h4>Find the Best Insurance at the Best Price!</h4>
    <p>Whether you are looking for life insurance, mortgage insurance or else you certainly want to pay the most advantageous price. Navigating among the many offers in the field of insurance can be a real headache.</p>
    <ul>
      <li><svg width="14" height="14"><circle cx="7" cy="7" r="7" fill="var(--red)"/><path d="M4 7l2 2 4-4" fill="none" stroke="#fff" stroke-width="2"/></svg>Permanent life insurance - term life insurance</li>
      <li><svg width="14" height="14"><circle cx="7" cy="7" r="7" fill="var(--red)"/><path d="M4 7l2 2 4-4" fill="none" stroke="#fff" stroke-width="2"/></svg>Disability Insurance - Disability Insurance</li>
      <li><svg width="14" height="14"><circle cx="7" cy="7" r="7" fill="var(--red)"/><path d="M4 7l2 2 4-4" fill="none" stroke="#fff" stroke-width="2"/></svg>Mortgage Insurance - loans</li>
      <li><svg width="14" height="14"><circle cx="7" cy="7" r="7" fill="var(--red)"/><path d="M4 7l2 2 4-4" fill="none" stroke="#fff" stroke-width="2"/></svg>Critical illness insurance</li>
    </ul>
    <span class="more" style="display:block;margin-top:12px">READ MORE &gt;&gt;</span>
  </div>
  <div class="prod-photo" role="img" aria-label="Smiling family with a young child sitting outdoors on the grass"></div>
</section>

<section class="blog">
  <h2 class="sec-title" style="top:40px">
    <svg width="10" height="18"><path d="M9 1L1 9l8 8" fill="none" stroke="#888" stroke-width="2"/></svg>
    <span style="color:var(--navy)">OUR <span>BLOG</span></span>
    <svg width="10" height="18"><path d="M1 1l8 8-8 8" fill="none" stroke="#888" stroke-width="2"/></svg>
  </h2>
  <article class="post" style="left:100px">
    <div class="thumb" role="img" aria-label="Couple meeting with an insurance advisor" style="background:linear-gradient(135deg,#5a6478,#c9a38a 60%,#b5373a)"><span class="date">05/04/2016</span></div>
    <h4>How to proceed?</h4>
    <p>Simply fill in the insurance quote online form above, clicking on the insurance category that fits your needs.</p>
    <span class="more">READ MORE &gt;&gt;</span>
  </article>
  <article class="post" style="left:354px">
    <div class="thumb" role="img" aria-label="Financial advisor reviewing documents with a senior couple" style="background:linear-gradient(135deg,#e6e2da,#b58a70 50%,#c0453c)"><span class="date">05/04/2016</span></div>
    <h4>Competent financial advisors security</h4>
    <p>Team Le Pont d'Oriole offers an innovative service in the field,..</p>
    <span class="more">READ MORE &gt;&gt;</span>
  </article>
  <article class="post" style="left:609px">
    <div class="thumb" role="img" aria-label="People discussing paperwork at a table" style="background:linear-gradient(135deg,#8c7658,#d3c0a6 50%,#6a5a48)"><span class="date">05/04/2016</span></div>
    <h4>The importance of not overpaying</h4>
    <p>Disbursing monthly or annually money for insurance is a considerable expense.</p>
    <span class="more">READ MORE &gt;&gt;</span>
  </article>
  <article class="post" style="left:863px">
    <div class="thumb" role="img" aria-label="Saving money concept image with a blue banner" style="background:linear-gradient(180deg,#2f8fd1,#8fc3e6 55%,#8b8f94)"><span class="date">05/04/2016</span></div>
    <h4>Insurance: ? How to find</h4>
    <p>The life insurance market premium may seem complex at first. Indeed, insurers offer a variety of products...</p>
    <span class="more">READ MORE &gt;&gt;</span>
  </article>
</section>

<section class="companies">
  <h2 class="sec-title" style="top:34px"><span style="color:var(--navy)">OUR <span>COMPANIES</span></span></h2>
  <svg class="abs" style="left:98px;top:114px" width="10" height="18"><path d="M9 1L1 9l8 8" fill="none" stroke="#888" stroke-width="2"/></svg>
  <svg class="abs" style="left:1088px;top:114px" width="10" height="18"><path d="M1 1l8 8-8 8" fill="none" stroke="#888" stroke-width="2"/></svg>
  <div class="partner" style="left:183px">Norvane</div>
  <div class="partner" style="left:354px">Altessa</div>
  <div class="partner" style="left:524px">Brivolt</div>
  <div class="partner" style="left:694px">Cimetra</div>
  <div class="partner" style="left:863px">Solbria</div>
</section>

<section class="offices">
  <div class="offices-bg" role="img" aria-label="Blue sky with clouds over a green meadow"></div>
  <div class="offices-people" role="img" aria-label="Happy family of four lying together on the grass"></div>
  <h2>OUR OFFICES</h2>
  <ul class="city-col" style="left:100px"><li><svg width="14" height="14"><circle cx="7" cy="7" r="7" fill="var(--red)"/><path d="M4 7l2 2 4-4" fill="none" stroke="#fff" stroke-width="2"/></svg>MONTREAL</li><li><svg width="14" height="14"><circle cx="7" cy="7" r="7" fill="var(--red)"/><path d="M4 7l2 2 4-4" fill="none" stroke="#fff" stroke-width="2"/></svg>QUEBEC</li><li><svg width="14" height="14"><circle cx="7" cy="7" r="7" fill="var(--red)"/><path d="M4 7l2 2 4-4" fill="none" stroke="#fff" stroke-width="2"/></svg>SHERBROOKE</li><li><svg width="14" height="14"><circle cx="7" cy="7" r="7" fill="var(--red)"/><path d="M4 7l2 2 4-4" fill="none" stroke="#fff" stroke-width="2"/></svg>GRANBY</li><li><svg width="14" height="14"><circle cx="7" cy="7" r="7" fill="var(--red)"/><path d="M4 7l2 2 4-4" fill="none" stroke="#fff" stroke-width="2"/></svg>BEAUCE</li></ul>
  <ul class="city-col" style="left:241px"><li><svg width="14" height="14"><circle cx="7" cy="7" r="7" fill="var(--red)"/><path d="M4 7l2 2 4-4" fill="none" stroke="#fff" stroke-width="2"/></svg>THREE RIVÈRES</li><li><svg width="14" height="14"><circle cx="7" cy="7" r="7" fill="var(--red)"/><path d="M4 7l2 2 4-4" fill="none" stroke="#fff" stroke-width="2"/></svg>PIEDMONT</li><li><svg width="14" height="14"><circle cx="7" cy="7" r="7" fill="var(--red)"/><path d="M4 7l2 2 4-4" fill="none" stroke="#fff" stroke-width="2"/></svg>SAGUENAY</li><li><svg width="14" height="14"><circle cx="7" cy="7" r="7" fill="var(--red)"/><path d="M4 7l2 2 4-4" fill="none" stroke="#fff" stroke-width="2"/></svg>GOODS</li><li><svg width="14" height="14"><circle cx="7" cy="7" r="7" fill="var(--red)"/><path d="M4 7l2 2 4-4" fill="none" stroke="#fff" stroke-width="2"/></svg>CHICOUTIMI</li></ul>
  <ul class="city-col" style="left:385px"><li><svg width="14" height="14"><circle cx="7" cy="7" r="7" fill="var(--red)"/><path d="M4 7l2 2 4-4" fill="none" stroke="#fff" stroke-width="2"/></svg>SEPT-ILES</li><li><svg width="14" height="14"><circle cx="7" cy="7" r="7" fill="var(--red)"/><path d="M4 7l2 2 4-4" fill="none" stroke="#fff" stroke-width="2"/></svg>ROUYN-NORANDA</li><li><svg width="14" height="14"><circle cx="7" cy="7" r="7" fill="var(--red)"/><path d="M4 7l2 2 4-4" fill="none" stroke="#fff" stroke-width="2"/></svg>VAL D'OR</li><li><svg width="14" height="14"><circle cx="7" cy="7" r="7" fill="var(--red)"/><path d="M4 7l2 2 4-4" fill="none" stroke="#fff" stroke-width="2"/></svg>GATINEAU</li><li><svg width="14" height="14"><circle cx="7" cy="7" r="7" fill="var(--red)"/><path d="M4 7l2 2 4-4" fill="none" stroke="#fff" stroke-width="2"/></svg>VICTORIAVILLE</li></ul>
  <ul class="city-col" style="left:548px"><li><svg width="14" height="14"><circle cx="7" cy="7" r="7" fill="var(--red)"/><path d="M4 7l2 2 4-4" fill="none" stroke="#fff" stroke-width="2"/></svg>AMQUI</li><li><svg width="14" height="14"><circle cx="7" cy="7" r="7" fill="var(--red)"/><path d="M4 7l2 2 4-4" fill="none" stroke="#fff" stroke-width="2"/></svg>WOLF RIVER</li><li><svg width="14" height="14"><circle cx="7" cy="7" r="7" fill="var(--red)"/><path d="M4 7l2 2 4-4" fill="none" stroke="#fff" stroke-width="2"/></svg>CHATEAUGUAY</li><li><svg width="14" height="14"><circle cx="7" cy="7" r="7" fill="var(--red)"/><path d="M4 7l2 2 4-4" fill="none" stroke="#fff" stroke-width="2"/></svg>LA PRAIRIE</li></ul>
</section>

<footer class="site-footer">
  <div class="f-brand">Le Pont d'Oriole</div>
  <div class="f-badge"></div>
  <div class="f-col hours" style="left:304px">
    <h5>Hours of Operation</h5>
    <div><span>Monday to Friday:</span><span>7am to 21hrs</span></div>
    <div><span>Sunday:</span><span>10hrs to 15hrs</span></div>
  </div>
  <div class="f-col news" style="left:548px">
    <h5>Newsletter</h5>
    <p>Register your email address to get information ablout us</p>
    <div class="email">Email Address</div>
    <div class="sub">SUBSCRIBE</div>
  </div>
  <div class="f-col contact-col" style="left:865px;top:42px">
    <h5 style="margin-bottom:6px">Contact Us</h5>
    <div><svg width="10" height="14" viewBox="0 0 10 14"><path d="M5 0a5 5 0 0 0-5 5c0 4 5 9 5 9s5-5 5-9a5 5 0 0 0-5-5z" fill="#ddd"/><circle cx="5" cy="5" r="2" fill="#232323"/></svg>48 Rue des Ormes, Val-Oriole, QC, G0X 4K7</div>
    <div><svg width="12" height="12" viewBox="0 0 14 14"><path d="M3 1l3 3-2 2c1 2 2 3 4 4l2-2 3 3-2 2C6 13 1 8 1 3z" fill="#ddd"/></svg>1-855-555-0142</div>
    <div><svg width="13" height="10" viewBox="0 0 14 10"><rect width="14" height="10" fill="#ddd"/><path d="M0 0l7 5 7-5" fill="none" stroke="#232323"/></svg>contact@lepontdoriole.ca</div>
  </div>
  <div class="f-bottom"></div>
  <div class="copy">Copyrights ©2016, Le Pont d'Oriole. All rights reserved.</div>
  <div class="social"><i></i><i></i><i></i><i></i></div>
</footer>

</body>
</html>
```